Harborlane Products Flyer

Harborlane Lending Group, Inc.
Licensed Mortgage Company
Serving the DMV since 1997
"You open the Harborlane, we'll carry the load"
We specialize in...
FHA Loans
* Credit Scores as low as 500
* 203K Renovation Loans
Conventional Loans
* As little as 1% Down
* Bank Statement for Self-Employed
Investor Loans
* DSCR, & Fix & Flip
* Commercial & New Construction
Other Programs
* HELOCS & Reverse Mortgages
Call today for a free consultation
(800) 914-6027
www.harborlanehomeloans.com
NMLS #731860

```html
<!DOCTYPE html>
<html lang="en">
<head>
<meta charset="utf-8">
<title>Harborlane Products Flyer</title>
<link href="https://fonts.googleapis.com/css2?family=Poppins:wght@400;500;600;700;800&display=swap" rel="stylesheet">
<style>
:root{
  --blue:#1f4699;
  --blue-dark:#18397f;
  --gold:#f2b95a;
  --gold-text:#e3a445;
  --sky:#7ea7d6;
  --ink:#222;
  --rule:#555;
  --white:#fff;
}
*{box-sizing:border-box;margin:0;padding:0}
html,body{width:960px;height:1200px;overflow:hidden;background:var(--white)}
body{font-family:"Poppins",sans-serif;color:var(--ink);position:relative}
.abs{position:absolute;white-space:nowrap}
.hero-art{position:absolute;left:0;top:0;width:960px;height:610px}
.brand{left:50px;top:92px;width:300px;display:flex;align-items:center;gap:12px;white-space:normal}
.brand-dot{width:40px;height:40px;border-radius:50%;background:var(--blue);flex:none}
.brand-name{font-weight:700;font-size:25px;line-height:1.15;color:var(--blue)}
.intro{left:62px;top:268px;color:var(--white);font-weight:500;font-size:18px;line-height:22px}
.intro-rule{left:62px;top:328px;width:280px;height:1px;background:rgba(255,255,255,.7)}
.headline{left:62px;top:342px;color:var(--white)}
.headline .lead{font-size:36px;font-weight:400;line-height:48px}
.headline .key{font-size:50px;font-weight:800;line-height:72px;letter-spacing:.5px;
  background:linear-gradient(180deg,#fff3c4 0%,#e9c25c 45%,#b8892a 100%);
  -webkit-background-clip:text;background-clip:text;color:transparent}
.headline .rest{font-size:46px;font-weight:800;line-height:52px;letter-spacing:.5px}
.spec-line{top:667px;height:1px;background:var(--rule)}
.spec-banner{left:273px;top:637px;width:412px;height:56px}
.spec-title{left:273px;top:637px;width:412px;height:56px;line-height:56px;text-align:center;color:var(--white);font-weight:600;font-size:34px}
.card{position:absolute;width:402px;height:140px}
.card-frame{position:absolute;left:0;top:0;width:402px;height:140px;overflow:visible}
.card-title{position:absolute;left:0;top:-2px;background:var(--white);padding-right:10px;font-weight:700;font-size:24px;line-height:28px;white-space:nowrap}
.t-gold{color:var(--gold-text)}
.t-blue{color:var(--blue)}
.icon-box{position:absolute;left:1px;top:38px;width:95px;height:101px;border-radius:6px;display:flex;align-items:center;justify-content:center}
.bg-blue{background:var(--blue)}
.bg-gold{background:var(--gold)}
.txt{position:absolute;font-size:19px;line-height:24px;white-space:nowrap}
.big{position:absolute;font-weight:700;line-height:1}
.dash{position:absolute;height:0;border-top:1px dashed #888}
.caps{position:absolute;font-size:17px;font-weight:500;line-height:24px;text-transform:uppercase;letter-spacing:.3px;white-space:nowrap}
.footer-call{left:68px;top:1095px;font-size:19px;line-height:25px}
.footer-call strong{color:var(--gold-text);font-weight:700}
.phone-icon{left:295px;top:1099px;width:40px;height:40px}
.phone-num{left:345px;top:1098px;font-size:27px;font-weight:600;line-height:40px}
.footer-div{left:576px;top:1095px;height:46px;border-left:1px dashed #888}
.web{left:602px;top:1093px;font-size:16px;line-height:26px;letter-spacing:.2px}
.web b{color:var(--blue);font-weight:700}
.nmls{left:602px;top:1122px;font-size:16px;font-weight:700;line-height:24px}
.base-bar{left:0;top:1187px;width:960px;height:13px;background:var(--blue)}
</style>
</head>
<body>

<svg class="hero-art" viewBox="0 0 1430 940" preserveAspectRatio="none">
  <defs>
    <linearGradient id="photoTone" x1="0" y1="0" x2="0" y2="1">
      <stop offset="0" stop-color="#b9ad9a"/>
      <stop offset="0.45" stop-color="#7d8a6a"/>
      <stop offset="1" stop-color="#4f8a2f"/>
    </linearGradient>
  </defs>
  <polygon points="0,357 512,357 642,152 1430,152 1430,940 0,940" fill="#1f4699"/>
  <polygon points="632,517 682,517 1000,940 878,940" fill="#f2b95a"/>
  <polygon points="990,910 1160,910 1175,940 1005,940" fill="#1f4699"/>
  <polygon points="1160,910 1430,910 1430,940 1175,940" fill="#f2b95a"/>
  <polygon points="812,0 1430,0 1430,897 925,897 582,405" fill="url(#photoTone)" stroke="#fff" stroke-width="12" stroke-linejoin="miter" role="img" aria-label="Photo: a smiling family of four celebrating in front of their new house, holding a home for sale sign"/>
</svg>

<div class="abs brand">
  <span class="brand-dot"></span>
  <span class="brand-name">Harborlane Lending Group, Inc.</span>
</div>

<p class="abs intro">Licensed Mortgage Company<br>Serving the DMV since 1997</p>
<div class="abs intro-rule"></div>

<h1 class="abs headline">
  <span class="lead" style="display:block">You open the</span>
  <span class="key" style="display:block">HARBORLANE</span>
  <span class="rest" style="display:block">WE'LL CARRY<br>THE LOAD</span>
</h1>

<div class="abs spec-line" style="left:71px;width:185px"></div>
<div class="abs spec-line" style="left:696px;width:193px"></div>
<svg class="abs spec-banner" viewBox="0 0 412 56" preserveAspectRatio="none" aria-hidden="true">
  <polygon points="0,0 412,0 397,56 15,56" fill="var(--sky)"/>
</svg>
<h2 class="abs spec-title">We specialize in...</h2>

<section class="card" style="left:65px;top:720px">
  <svg class="card-frame" viewBox="0 0 402 140" aria-hidden="true"><path d="M0 12 H378 L400 32 V126 H330" fill="none" stroke="var(--rule)" stroke-width="1.2"/></svg>
  <h3 class="card-title t-gold">FHA Loans</h3>
  <div class="icon-box bg-blue">
    <svg width="62" height="62" viewBox="0 0 62 62" aria-hidden="true">
      <circle cx="34" cy="20" r="15" fill="#fff"/>
      <text x="34" y="27" text-anchor="middle" font-family="Poppins,sans-serif" font-weight="700" font-size="20" fill="var(--blue)">$</text>
      <path d="M4 44 h8 v16 h-8z M14 46 h16 c4 0 6 4 2 5 h-10 M14 58 h22 l20 -12 c3 -2 1 -6 -3 -5 l-15 7" fill="none" stroke="#fff" stroke-width="3.5" stroke-linecap="round" stroke-linejoin="round"/>
    </svg>
  </div>
  <p class="txt" style="left:114px;top:35px">Credit Scores<br>as low as</p>
  <span class="big t-blue" style="left:270px;top:38px;font-size:48px">500</span>
  <div class="dash" style="left:114px;top:87px;width:246px"></div>
  <span class="big t-blue" style="left:114px;top:94px;font-size:50px">203k</span>
  <p class="txt" style="left:246px;top:95px">Renovation<br>Loans</p>
</section>

<section class="card" style="left:492px;top:722px">
  <svg class="card-frame" viewBox="0 0 402 140" aria-hidden="true"><path d="M0 12 H378 L400 32 V126 H282" fill="none" stroke="var(--rule)" stroke-width="1.2"/></svg>
  <h3 class="card-title t-blue">Investor Loans</h3>
  <div class="icon-box bg-gold">
    <svg width="60" height="60" viewBox="0 0 60 60" aria-hidden="true">
      <path d="M6 54 H54" stroke="#222" stroke-width="3"/>
      <rect x="10" y="34" width="9" height="18" fill="#222"/>
      <rect x="25" y="24" width="9" height="28" fill="#222"/>
      <rect x="40" y="12" width="9" height="40" fill="#222"/>
    </svg>
  </div>
  <p class="caps" style="left:112px;top:44px">DSCR, &amp; Fix &amp; Flip</p>
  <div class="dash" style="left:112px;top:87px;width:246px"></div>
  <p class="caps" style="left:112px;top:94px">Commercial &amp; New<br>Construction</p>
</section>

<section class="card" style="left:65px;top:897px">
  <svg class="card-frame" viewBox="0 0 402 140" aria-hidden="true"><path d="M0 12 H378 L400 32 V126 H382" fill="none" stroke="var(--rule)" stroke-width="1.2"/></svg>
  <h3 class="card-title t-blue">Conventional Loans</h3>
  <div class="icon-box bg-gold">
    <svg width="62" height="62" viewBox="0 0 62 62" aria-hidden="true">
      <path d="M18 20 L32 8 L46 20 V34 H18 Z" fill="none" stroke="#222" stroke-width="3.5" stroke-linejoin="round"/>
      <text x="32" y="32" text-anchor="middle" font-family="Poppins,sans-serif" font-weight="700" font-size="14" fill="#222">$</text>
      <path d="M4 44 h8 v16 h-8z M14 46 h16 c4 0 6 4 2 5 h-10 M14 58 h22 l20 -12 c3 -2 1 -6 -3 -5 l-15 7" fill="none" stroke="#222" stroke-width="3.5" stroke-linecap="round" stroke-linejoin="round"/>
    </svg>
  </div>
  <p class="txt" style="left:114px;top:35px">As little<br>as</p>
  <span class="big" style="left:203px;top:38px;font-size:48px;color:var(--gold)">1%</span>
  <span class="txt" style="left:276px;top:58px;font-weight:700">Down</span>
  <div class="dash" style="left:114px;top:87px;width:246px"></div>
  <p class="txt" style="left:114px;top:94px">Bank<br>Statement for</p>
  <p class="txt t-gold" style="left:271px;top:94px;font-weight:700;font-size:17px">SELF<br>EMPLOYED</p>
</section>

<section class="card" style="left:492px;top:897px">
  <svg class="card-frame" viewBox="0 0 402 140" aria-hidden="true"><path d="M0 12 H378 L400 32 V126 H94" fill="none" stroke="var(--rule)" stroke-width="1.2"/></svg>
  <h3 class="card-title t-gold">Other Programs</h3>
  <div class="icon-box bg-blue">
    <svg width="62" height="62" viewBox="0 0 62 62" aria-hidden="true">
      <circle cx="31" cy="22" r="13" fill="none" stroke="#fff" stroke-width="3.5"/>
      <polygon points="31,14 33.5,19.5 39,20 35,24 36,30 31,27 26,30 27,24 23,20 28.5,19.5" fill="#fff"/>
      <path d="M10 30 c0 14 8 20 14 26 M52 30 c0 14 -8 20 -14 26" fill="none" stroke="#fff" stroke-width="3.5" stroke-linecap="round"/>
    </svg>
  </div>
  <p class="caps" style="left:112px;top:54px">HELOCS &amp;<br>Reverse Mortgages</p>
</section>

<p class="abs footer-call">CALL TODAY FOR A<br><strong>FREE CONSULTATION</strong></p>
<svg class="abs phone-icon" viewBox="0 0 42 42" aria-hidden="true">
  <circle cx="21" cy="21" r="21" fill="var(--blue)"/>
  <path d="M14 12 c-2 2 -2 6 2 11 s9 8 11 6 l2 -2 -4 -4 -2 2 c-2 -1 -4 -3 -5 -5 l2 -2 -4 -4z" fill="#fff"/>
</svg>
<p class="abs phone-num">(800) 914-6027</p>
<div class="abs footer-div"></div>
<p class="abs web">www.<b>harborlanehomeloans</b>.com</p>
<p class="abs nmls">NMLS #731860</p>
<div class="abs base-bar"></div>

</body>
</html>
```